Tall ridge firewood

It a new firewood outlet in Jindabyne nsw that will only sell top hardwood firewood (ironbark , red gum, grey gum, an box mix. I would like to see a web page the we can do order online payment for delivery. It will all so need to have photos of the firewood. I all so have logo for tall ridge firewood
Must have a modem look but easy to use I would like to see a black back ground of some sort.

Here are some other firewood web pages for ideas and firewood info
http://www.example-logpile.com.au
http://www.example-stackwood.com.au
http://www.example-splitlog.com.au
http://www.example-kendaltimber.com.au/firewood

Industry/Entity Type

Firewood

```html
<!DOCTYPE html>
<html lang="en">
<head>
<meta charset="utf-8">
<title>Tall Ridge Firewood</title>
<link href="https://fonts.googleapis.com/css2?family=Arimo:wght@400;700&family=Roboto+Condensed:wght@400;700&display=swap" rel="stylesheet">
<style>
:root{
  --ink:#151515;
  --panel:#1c1c1c;
  --blue:#1a72bf;
  --blue-dark:#145c9c;
  --white:#ffffff;
  --muted:#d8d8d8;
  --line:#3a3a3a;
  --fire:#e8561a;
}
*{box-sizing:border-box;margin:0;padding:0}
html,body{width:966px;height:1200px;overflow:hidden}
body{position:relative;background:var(--ink);font-family:"Arimo",Arial,sans-serif;color:var(--white);font-size:10px}
.abs{position:absolute}

/* header */
.site-header{position:absolute;left:0;top:0;width:966px;height:140px;background:linear-gradient(#161616,#101010)}
.brand{position:absolute;left:123px;top:0;width:174px;height:139px;background:var(--white);display:flex;flex-direction:column;align-items:center;justify-content:center;gap:10px}
.brand-dot{width:62px;height:62px;border-radius:50%;background:var(--blue)}
.brand-name{font-family:"Roboto Condensed",sans-serif;font-weight:700;font-size:15px;color:var(--blue);text-transform:uppercase}
.topbar{position:absolute;top:21px;font-size:9px;display:flex;align-items:center;gap:6px}
.topbar b{font-size:10px}
.topbar a{color:var(--white)}
.search{position:absolute;left:540px;top:62px;width:190px;height:20px;display:flex}
.search-field{flex:1;background:var(--white);color:#666;font-size:9px;padding:5px 7px}
.search-btn{width:20px;background:var(--blue);display:flex;align-items:center;justify-content:center}
.btn-dark{position:absolute;background:linear-gradient(#3a3a3a,#222);color:var(--white);font-size:9px;font-weight:700;display:flex;align-items:center;justify-content:center;border-radius:2px;text-transform:uppercase}
.btn-light{position:absolute;background:linear-gradient(#fff,#dcdcdc);color:#222;font-size:9px;font-weight:700;display:flex;align-items:center;justify-content:center;border-radius:2px;text-transform:uppercase}
.main-nav{position:absolute;top:115px;left:384px;display:flex;gap:26px;font-size:9px;text-transform:uppercase}
.main-nav .active{color:var(--blue)}
.nav-rule{position:absolute;left:0;top:139px;width:966px;height:3px;background:var(--blue)}

/* hero */
.hero{position:absolute;left:0;top:142px;width:966px;height:352px;background:radial-gradient(ellipse 48% 78% at 50% 70%,#ffb020 0%,#f06a10 30%,#b3300a 55%,#4a2418 75%,#5c4236 90%,#3e2f28 100%)}
.hero-caption{position:absolute;left:342px;top:304px;width:282px;height:31px;background:var(--white);display:flex;align-items:center;justify-content:center;font-size:19px;color:var(--ink)}
.hero-caption span{color:var(--blue)}
.hero-arrow{position:absolute;top:301px;width:38px;height:38px;border-radius:50%;background:rgba(210,210,210,.55);display:flex;align-items:center;justify-content:center}
.hero-rule{position:absolute;left:0;top:494px;width:966px;height:3px;background:#8a8a8a}

/* products */
.products{position:absolute;left:0;top:497px;width:966px;height:524px;background:linear-gradient(90deg,#161616,#202020 50%,#161616)}
.product{position:absolute;top:26px;width:140px;text-align:center}
.product-photo{width:122px;height:122px;border-radius:50%;margin:0 auto;border:3px solid #cfcfcf}
.product.is-active .product-photo{border-color:var(--blue)}
.product-name{font-family:"Roboto Condensed",sans-serif;font-size:12px;margin-top:14px;text-transform:uppercase}
.product-price{font-size:9px;margin-top:2px}
.product-price b{color:var(--blue);font-size:13px;margin-left:2px}
.product .btn-dark,.product .btn-light{left:42px;top:196px;width:57px;height:22px}
.section-rule{position:absolute;left:129px;top:265px;width:707px;height:1px;background:var(--line)}
.btn-blue{position:absolute;left:409px;top:252px;width:148px;height:26px;background:var(--blue);color:var(--white);font-size:11px;display:flex;align-items:center;justify-content:center;border-radius:2px}

.col{position:absolute;top:311px}
.col h2{font-family:"Roboto Condensed",sans-serif;font-weight:400;font-size:18px;text-transform:uppercase;margin-bottom:17px}
.col p{font-size:9px;line-height:11px;color:var(--muted);margin-bottom:11px}
.list-item{display:flex;gap:8px;margin-bottom:13px;font-size:9px;line-height:11px;color:var(--muted)}
.list-num{font-family:"Roboto Condensed",sans-serif;color:var(--blue);font-size:17px;width:21px;line-height:16px}
.col-divider{position:absolute;top:312px;width:1px;height:171px;background:var(--line)}
.col .btn-dark{width:71px;height:19px}

/* footer */
.site-footer{position:absolute;left:0;top:1021px;width:966px;height:149px;background:var(--blue)}
.foot-col{position:absolute;top:20px}
.foot-col h3{font-size:8.5px;font-weight:700;text-transform:uppercase;margin-bottom:10px}
.foot-col li{list-style:none;font-size:8.5px;line-height:13px}
.foot-divider{position:absolute;top:19px;width:1px;height:104px;background:rgba(255,255,255,.25)}
.pay-card{display:inline-block;width:29px;height:18px;background:var(--white);border-radius:2px;margin-right:6px}
.social{display:inline-block;width:21px;height:21px;background:rgba(255,255,255,.85);margin-right:4px}
.testimonial h3{font-size:13px;text-transform:none;margin-bottom:9px}
.testimonial p{font-size:9px;line-height:11px;width:235px;margin-bottom:9px}
.copyright{position:absolute;left:0;top:1170px;width:966px;height:30px;background:#121212;border-top:2px solid #2a2a2a;display:flex;align-items:center;justify-content:center;font-size:8.5px}
</style>
</head>
<body>

<header class="site-header">
  <div class="brand">
    <div class="brand-dot"></div>
    <div class="brand-name">Tall Ridge Firewood</div>
  </div>

  <div class="topbar" style="left:367px">
    <svg width="11" height="9" viewBox="0 0 11 9"><path d="M1 3 Q5.5 -1 10 3 L8.5 4.5 L7 3.5 L4 3.5 L2.5 4.5 Z M3 5 H8 L9 9 H2 Z" fill="#aaa"/></svg>
    <span>CALL US - <b>0400 318 527</b></span>
  </div>
  <div class="topbar" style="left:518px">
    <svg width="11" height="8" viewBox="0 0 11 8"><rect x=".5" y=".5" width="10" height="7" fill="none" stroke="#aaa"/><path d="M.5 .5 L5.5 4.5 L10.5 .5" fill="none" stroke="#aaa"/></svg>
    <span>MAIL US - <a href="#">info@tallridgefirewood.example</a></span>
  </div>
  <div class="topbar" style="left:732px">
    <svg width="11" height="10" viewBox="0 0 11 10"><path d="M0 1 H2 L3.5 6.5 H9.5 L10.5 2.5 H2.8" fill="none" stroke="#aaa"/><circle cx="4" cy="8.5" r="1" fill="#aaa"/><circle cx="9" cy="8.5" r="1" fill="#aaa"/></svg>
    <span>MY CART - 0 ITEM (S)</span>
  </div>

  <div class="search">
    <div class="search-field">Find Firewood Products ..</div>
    <div class="search-btn">
      <svg width="11" height="11" viewBox="0 0 11 11"><circle cx="4.5" cy="4.5" r="3.3" fill="none" stroke="#fff" stroke-width="1.6"/><path d="M7 7 L10 10" stroke="#fff" stroke-width="1.8"/></svg>
    </div>
  </div>
  <div class="btn-dark" style="left:752px;top:62px;width:84px;height:19px">Order Online</div>

  <nav class="main-nav">
    <span class="active">Home</span><span>About Us</span><span>Products</span><span>Accessories</span><span>Delivery</span><span>FAQ`S</span><span>Contact Us</span>
  </nav>
  <svg class="abs" style="left:390px;top:134px" width="9" height="5" viewBox="0 0 9 5"><path d="M0 5 L4.5 0 L9 5Z" fill="#1a72bf"/></svg>
  <div class="nav-rule"></div>
</header>

<section class="hero" role="img" aria-label="Photo of a hardwood fire burning inside a brick oven arch">
  <div class="hero-arrow" style="left:46px">
    <svg width="10" height="20" viewBox="0 0 10 20"><path d="M8 1 L2 10 L8 19" fill="none" stroke="#333" stroke-width="1.3"/></svg>
  </div>
  <div class="hero-caption"><span>TOP</span>&nbsp;HARDWOOD&nbsp;<span>FIREWOOD</span></div>
  <div class="hero-arrow" style="left:882px">
    <svg width="10" height="20" viewBox="0 0 10 20"><path d="M2 1 L8 10 L2 19" fill="none" stroke="#333" stroke-width="1.3"/></svg>
  </div>
</section>
<div class="hero-rule" style="top:493px"></div>

<main class="products">
  <div class="product is-active" style="left:121px">
    <div class="product-photo" role="img" aria-label="Close-up photo of split ironbark" style="background:radial-gradient(circle at 50% 45%,#b06a3a,#5a2e16 70%,#2a1a10)"></div>
    <div class="product-name">Ironbark</div>
    <div class="product-price">ONLY &nbsp;-&nbsp; <b>$12.30</b></div>
    <div class="btn-dark">More</div>
  </div>
  <div class="product" style="left:315px">
    <div class="product-photo" role="img" aria-label="Photo of a pile of red gum logs" style="background:radial-gradient(circle at 50% 45%,#b36a55,#6e3a2e 70%,#3a2420)"></div>
    <div class="product-name">Red Gum</div>
    <div class="product-price">ONLY &nbsp;-&nbsp; <b>$15.30</b></div>
    <div class="btn-light">More</div>
  </div>
  <div class="product" style="left:510px">
    <div class="product-photo" role="img" aria-label="Photo of a stack of grey gum logs" style="background:radial-gradient(circle at 50% 45%,#9aa2ac,#5e6670 70%,#3a3f46)"></div>
    <div class="product-name">Grey Gum</div>
    <div class="product-price">ONLY &nbsp;-&nbsp; <b>$12.30</b></div>
    <div class="btn-light">More</div>
  </div>
  <div class="product" style="left:704px">
    <div class="product-photo" role="img" aria-label="Photo of a fire burning in a fireplace grate" style="background:radial-gradient(circle at 50% 55%,#f5a030,#8a3a14 40%,#2a201c 70%,#4a4440)"></div>
    <div class="product-name">Box Mix</div>
    <div class="product-price">ONLY &nbsp;-&nbsp; <b>$12.30</b></div>
    <div class="btn-light">More</div>
  </div>

  <div class="section-rule"></div>
  <div class="btn-blue">VIEW ALL OUR PRODUCTS</div>

  <div class="col" style="left:129px;width:180px">
    <h2>Welcome To Our Site</h2>
    <p>Lorem ipsum dolor sit amet, consectetur adipisicing elit, sed do eiusmod tempor incididunt ut labore et dolore magna aliqua. Ut enim ad minim veniam, quis nostrud exercitation ullamco.</p>
    <p>Duis aute irure dolor in reprehenderit in voluptate velit esse cillum dolore eu fugiat nulla pariatur ...</p>
    <div class="btn-dark" style="left:0;top:152px">Read More</div>
  </div>
  <div class="col-divider" style="left:351px"></div>

  <div class="col" style="left:390px;width:200px">
    <h2>Why Choose Us?</h2>
    <div class="list-item"><svg width="10" height="9" viewBox="0 0 10 9"><path d="M1 4.5 L4 7.5 L9 1" fill="none" stroke="#999" stroke-width="2"/></svg><span>Lorem ipsum dolor sit amet, consectetur<br>adipisicing elit.</span></div>
    <div class="list-item"><svg width="10" height="9" viewBox="0 0 10 9"><path d="M1 4.5 L4 7.5 L9 1" fill="none" stroke="#999" stroke-width="2"/></svg><span>Lorem ipsum dolor sit amet, consectetur<br>adipisicing elit.</span></div>
    <div class="list-item"><svg width="10" height="9" viewBox="0 0 10 9"><path d="M1 4.5 L4 7.5 L9 1" fill="none" stroke="#999" stroke-width="2"/></svg><span>Lorem ipsum dolor sit amet, consectetur<br>adipisicing elit.</span></div>
    <div class="btn-dark" style="left:0;top:152px">Read More</div>
  </div>
  <div class="col-divider" style="left:609px"></div>

  <div class="col" style="left:642px;width:200px">
    <h2>Latest News</h2>
    <div class="list-item"><span class="list-num">01</span><span>Lorem ipsum dolor sit amet, consectetur<br>adipisicing elit.</span></div>
    <div class="list-item"><span class="list-num">02</span><span>Lorem ipsum dolor sit amet, consectetur<br>adipisicing elit.</span></div>
    <div class="list-item"><span class="list-num">03</span><span>Lorem ipsum dolor sit amet, consectetur<br>adipisicing elit.</span></div>
    <div class="btn-dark" style="left:0;top:152px;width:60px">View All</div>
  </div>
</main>

<footer class="site-footer">
  <div class="foot-col" style="left:130px">
    <h3>Navigation</h3>
    <ul><li>» &nbsp;Home</li><li>» &nbsp;About Us</li><li>» &nbsp;Products</li><li>» &nbsp;Accessories</li><li>» &nbsp;Contact Us</li></ul>
  </div>
  <div class="foot-divider" style="left:229px"></div>
  <div class="foot-col" style="left:264px">
    <h3>Order Online</h3>
    <ul><li>» &nbsp;Terms &amp; Conditions</li><li>» &nbsp;Delivery</li><li>» &nbsp;Faq`s</li></ul>
  </div>
  <div class="foot-divider" style="left:385px"></div>
  <div class="foot-col" style="left:428px">
    <h3>Payment Option</h3>
    <div><span class="pay-card"></span><span class="pay-card"></span><span class="pay-card"></span></div>
    <h3 style="margin-top:22px">Follow Us On</h3>
    <div><span class="social"></span><span class="social"></span><span class="social"></span><span class="social"></span></div>
  </div>
  <div class="foot-divider" style="left:570px"></div>
  <div class="foot-col testimonial" style="left:608px;top:16px">
    <h3>Happy Client`s</h3>
    <p>Lorem ipsum dolor sit amet, consectetur adipisicing elit, sed do eiusmod tempor incididunt ut labore et dolore magna aliqua.</p>
    <p><b>Sam.</b> 15/06/13</p>
    <div class="btn-light" style="left:1px;top:112px;width:70px;height:19px">Read More</div>
  </div>
</footer>

<div class="copyright">COPYRIGHT © TALL RIDGE FIREWOOD 2013. ALL RIGHT RESERVED.</div>

</body>
</html>
```